A creative, unique invitation card for destination wedding

We are looking for a creative wedding invitation card for our destination wedding at Koh Samui. Wedding theme colour is in blue grey (slate blue) and khaki. We have included the one idea we have for the wedding invite (please ignore the fonts and colour). However, we would love to explore more unqiue ideas and design. Please include the photos attached and feel free to choose between the duplicates.

Target Market(s)

Friends and families

Industry/Entity Type

Wedding

Font styles to use
Sans Serif
Decorative
Script

Colors

Designer to choose colors to be used in the design.

Requirements
Must have
• Card should fit into a 110 X 220 cm envelope
Nice to have
• One design with blue grey/slate blue colour palette
Should not have
• Avoid dye cut
• Cartoons
• Primary colours

```html
<!DOCTYPE html>
<html lang="en">
<head>
<meta charset="utf-8">
<title>Wedding Invitation – Mara &amp; Evan</title>
<link href="https://fonts.googleapis.com/css2?family=Tinos&family=Great+Vibes&family=Bebas+Neue&family=Quicksand:wght@300;700&family=Oswald:wght@300;600&display=swap" rel="stylesheet">
<style>
  :root{
    --page:#ffffff;
    --slate:#9eb1bd;
    --ink:#3d3b3c;
    --paper:#ffffff;
    --photo-light:#cfcfcf;
    --photo-dark:#6e6e6e;
  }
  html,body{margin:0;padding:0;width:1200px;height:1200px;overflow:hidden;background:var(--page);}
  .card{position:absolute;left:325px;top:58px;width:541px;height:1084px;background:var(--paper);}
  .panel{position:absolute;left:0;top:0;width:344px;height:100%;background:var(--slate);}
  .line{position:absolute;left:22px;width:310px;text-align:center;line-height:1;white-space:nowrap;}
  .serif{font-family:"Tinos",serif;color:var(--ink);}
  .l-together{top:122px;font-size:54px;}
  .l-with{top:177px;font-size:51px;}
  .l-families{top:224px;font-size:64px;}
  .name-script{top:318px;font-family:"Great Vibes",cursive;font-size:80px;color:var(--paper);}
  .amp{top:432px;font-family:"Tinos",serif;font-size:58px;color:var(--ink);}
  .name-block{top:498px;font-family:"Bebas Neue",sans-serif;font-size:88px;color:var(--paper);letter-spacing:1px;word-spacing:14px;}
  .l-invite{top:614px;font-size:51px;}
  .l-celebrate{top:668px;font-size:43px;}
  .l-marriage{top:721px;font-size:36px;}
  .date-day{top:765px;font-family:"Quicksand",sans-serif;font-weight:700;font-size:48px;color:var(--paper);}
  .date-time{top:815px;font-family:"Quicksand",sans-serif;font-weight:300;font-size:32px;color:var(--paper);}
  .venue{position:absolute;left:22px;width:310px;top:860px;text-align:center;font-family:"Oswald",sans-serif;font-weight:300;font-size:23px;line-height:33px;color:var(--ink);}
  .venue strong{font-weight:600;}
  .venue em{font-weight:600;color:var(--paper);}
  .photo{position:absolute;left:355px;width:158px;}
  .photo-1{top:89px;height:211px;background:linear-gradient(90deg,#9a9a9a,#e6e6e6 50%,#8a8a8a);}
  .photo-2{top:320px;height:212px;background:linear-gradient(180deg,#e2e2e2,#bdbdbd 45%,#8f8f8f 60%,#b5b5b5);}
  .photo-3{top:554px;height:210px;background:linear-gradient(180deg,#e4e4e4,#a9a9a9 55%,#c0c0c0);}
  .photo-4{top:784px;height:211px;background:linear-gradient(180deg,#7a7a7a,#c9c9c9 40%,#a5a5a5 70%,#4e4e4e);}
</style>
</head>
<body>
<div class="card">
  <section class="panel">
    <div class="line serif l-together">TOGETHER</div>
    <div class="line serif l-with">WITH THEIR</div>
    <div class="line serif l-families">FAMILIES</div>
    <div class="line name-script">Mara Lin</div>
    <div class="line amp">&amp;</div>
    <div class="line name-block">EVAN SOH</div>
    <div class="line serif l-invite">INVITE YOU</div>
    <div class="line serif l-celebrate">TO CELEBRATE</div>
    <div class="line serif l-marriage">THEIR MARRIAGE</div>
    <div class="line date-day">Thursday, 21</div>
    <div class="line date-time">June 2018 at 16:30</div>
    <p class="venue">The evening <strong>Serene Cove</strong><br><strong>Koh Samui Resort</strong> Dinner,<br><em>dancing and fun to follow</em></p>
  </section>
  <div class="photo photo-1" role="img" aria-label="Couple holding hands, engagement ring in view"></div>
  <div class="photo photo-2" role="img" aria-label="Couple walking along a beach towards a headland"></div>
  <div class="photo photo-3" role="img" aria-label="Couple seated on a rock facing the sea"></div>
  <div class="photo photo-4" role="img" aria-label="Aerial view of waves, beach and palm trees"></div>
</div>
</body>
</html>
```